Brand Identity Stationary Package

Hello I'm looking for a full branding package for my Property Management Company. I have a logo but looking to have the following
Business Card
Email signature
Facebook cover photo
Letterhead (word.doc)
#10 Envelope
Pocket Folder - link to 9x12 pocket folder design specs https://www.printorbit-example.ca/marketing-materials/presentation-folders
would like everything to match and be brand identifiable. The company looks after residential properties/apartments and some commercial properties. Attached is a zip of the files.
For Business Card
Name: Gareth Lindqvist
Position: Operations Manager
Number: 1 (555) 384-2917
Email: Gareth@harborkey-example.ca
Website: Harborkey-example.ca
Property Management

```html
<!DOCTYPE html>
<html lang="en">
<head>
<meta charset="utf-8">
<title>Harborkey Property Management – #10 Envelope</title>
<link rel="stylesheet" href="https://fonts.googleapis.com/css2?family=Montserrat:wght@500;600&family=Source+Sans+3:wght@400&display=swap">
<style>
  :root {
    --backdrop: #d2d1d1;
    --paper: #f3f2f2;
    --brand-green: #80a541;
    --ink: #141414;
    --white: #ffffff;
  }
  * { margin: 0; padding: 0; box-sizing: border-box; }
  html, body { width: 1200px; height: 1050px; overflow: hidden; }
  body { background: var(--backdrop); position: relative; }

  .envelope {
    position: absolute;
    left: 145px;
    width: 910px;
    height: 390px;
    background: var(--paper);
    overflow: hidden;
  }
  .envelope--back { top: 105px; }
  .envelope--front { top: 555px; }
  .envelope svg.shape { position: absolute; inset: 0; }

  .wordmark {
    position: absolute;
    font-family: "Montserrat", sans-serif;
    font-weight: 600;
    line-height: 1;
  }
  .wordmark__name { display: block; white-space: nowrap; }
  .wordmark__tagline {
    display: block;
    font-weight: 500;
    white-space: nowrap;
  }

  .envelope--back .wordmark {
    left: 0; right: 0; top: 30px;
    text-align: center;
    color: var(--white);
  }
  .envelope--back .wordmark__name { font-size: 47px; letter-spacing: 0.06em; }
  .envelope--back .wordmark__tagline { font-size: 11px; letter-spacing: 0.62em; margin-top: 10px; padding-left: 0.62em; }

  .envelope--front .wordmark {
    left: 34px; top: 44px;
    color: var(--ink);
  }
  .envelope--front .wordmark__name { font-size: 37px; letter-spacing: 0.06em; }
  .envelope--front .wordmark__tagline { font-size: 9px; letter-spacing: 0.72em; margin-top: 6px; }

  .contact-list {
    position: absolute;
    left: 34px; top: 133px;
    list-style: none;
    font-family: "Source Sans 3", sans-serif;
    font-size: 19px;
    color: var(--ink);
  }
  .contact-list li {
    display: flex;
    align-items: center;
    height: 26px;
  }
  .contact-list svg { width: 17px; height: 15px; margin-right: 12px; flex: none; }
</style>
</head>
<body>

  <section class="envelope envelope--back" aria-label="Envelope back">
    <svg class="shape" viewBox="0 0 910 390" aria-hidden="true">
      <path d="M0 0 H910 L885 92 Q870 131 830 131 H80 Q40 131 25 92 Z" fill="var(--brand-green)"/>
    </svg>
    <div class="wordmark">
      <span class="wordmark__name">HARBORKEY</span>
      <span class="wordmark__tagline">PROPERTY MANAGEMENT</span>
    </div>
  </section>

  <section class="envelope envelope--front" aria-label="Envelope front">
    <svg class="shape" viewBox="0 0 910 390" aria-hidden="true">
      <path d="M0 341 Q450 378 910 341 V390 H0 Z" fill="var(--brand-green)"/>
      <path d="M180 350 Q560 362 910 325 V337 Q560 365 180 350 Z" fill="var(--ink)"/>
    </svg>
    <div class="wordmark">
      <span class="wordmark__name">HARBORKEY</span>
      <span class="wordmark__tagline">PROPERTY MANAGEMENT</span>
    </div>
    <ul class="contact-list">
      <li>
        <svg viewBox="0 0 17 15" aria-hidden="true"><path d="M1 5 Q8.5 -1 16 5 L14 7 L12 5 V4 Q8.5 2.5 5 4 V5 L3 7 Z M4 8 H13 L15 14 H2 Z" fill="var(--brand-green)"/></svg>
        1 (555) 384-2917
      </li>
      <li>
        <svg viewBox="0 0 17 15" aria-hidden="true"><rect x="1" y="3" width="15" height="10" fill="var(--brand-green)"/><path d="M1 3 L8.5 9 L16 3 M1 13 L6.5 8 M16 13 L10.5 8" stroke="var(--paper)" stroke-width="1.2" fill="none"/></svg>
        Gareth@harborkey-example.ca
      </li>
      <li>
        <svg viewBox="0 0 17 15" aria-hidden="true"><circle cx="8.5" cy="7.5" r="7" fill="var(--brand-green)"/><ellipse cx="8.5" cy="7.5" rx="3" ry="7" fill="none" stroke="var(--paper)" stroke-width="1"/><path d="M1.5 7.5 H15.5" stroke="var(--paper)" stroke-width="1"/></svg>
        www.Harborkey-example.ca
      </li>
    </ul>
  </section>

</body>
</html>
```